BRIGHTHOLD PROPERTY MANAGEMENT INC. WEBSITE

Please make the website more family-friendly.

I want a website to help me build my property management business by adding listing properties and creating an online application. Im open to any other ideas.
I want a WordPress designer to code it.

Here is my current website. www.brighthold.biz

IDEA: I like the website design https://www.pelicanclimateservices.com/

Thank you

Tom

Number of Pages Required

5+ page

```html
<!DOCTYPE html>
<html lang="en">
<head>
<meta charset="utf-8">
<title>Brighthold Property Management</title>
<link href="https://fonts.googleapis.com/css2?family=Cinzel:wght@400;500;600&family=Roboto:wght@400;500;700&display=swap" rel="stylesheet">
<style>
:root{
  --red:#c0171f;
  --red-dark:#a91219;
  --black:#0b0b0b;
  --ink:#222;
  --muted:#666;
  --grey-tab:#6f6f6f;
  --line:#d6d6d6;
  --white:#fff;
  --footer:#161616;
}
*{margin:0;padding:0;box-sizing:border-box}
html,body{width:1200px;height:5259px;overflow:hidden}
body{position:relative;font-family:'Roboto',Arial,sans-serif;color:var(--ink);background:var(--white)}
.abs{position:absolute}
.serif{font-family:'Cinzel',Georgia,serif}

/* header */
.header{left:0;top:0;width:1200px;height:122px;background:var(--white)}
.brand{left:108px;top:26px;width:170px;text-align:center}
.brand-name{font-family:'Cinzel',Georgia,serif;font-weight:600;color:var(--red);font-size:22px;letter-spacing:.5px;display:block}
.brand-tag{font-size:6.5px;letter-spacing:.6px;color:var(--red);display:block;margin-top:2px}
.social{display:flex;gap:10px}
.social span{width:30px;height:30px;border:1.5px solid var(--red);border-radius:50%;display:block}
.header .social{left:545px;top:17px}
.call{left:786px;top:12px;display:flex;align-items:center;gap:12px}
.call small{display:block;font-size:12px;font-weight:500;color:var(--ink)}
.call strong{display:block;font-size:20px;color:var(--red);font-weight:700}
.nav{left:322px;top:72px;width:878px;height:50px;background:var(--black);display:flex;align-items:stretch;padding-left:0}
.nav a{color:var(--white);text-decoration:none;font-size:12.5px;font-weight:700;display:flex;align-items:center;padding:0 13px}
.nav a.active{background:var(--red);padding:0 16px}

/* hero */
.hero{left:0;top:122px;width:1200px;height:648px;background:linear-gradient(100deg,#3a3a36 0%,#7a746c 35%,#cfcac4 60%,#e9e6e2 100%)}
.hero-title{left:112px;top:282px;color:var(--white);font-family:'Cinzel',Georgia,serif;font-size:56px;line-height:60px;font-weight:500}
.btn-light{left:112px;top:481px;width:152px;height:42px;background:var(--white);color:var(--red);font-size:12px;font-weight:700;display:flex;align-items:center;justify-content:center}
.slide-ctrl{left:0;top:718px;width:192px;height:50px;background:var(--black);color:var(--white);font-size:12px;display:flex;align-items:center;gap:10px;padding-left:30px}
.subscribe{left:660px;top:718px;width:540px;height:56px;background:var(--white);box-shadow:0 4px 14px rgba(0,0,0,.12)}
.subscribe-input{left:34px;top:12px;width:336px;height:56px;background:#f1f1f1;color:#999;font-size:12px;display:flex;align-items:center;padding-left:26px}
.subscribe-btn{left:368px;top:12px;width:144px;height:56px;background:var(--red);color:var(--white);font-size:12px;font-weight:700;display:flex;align-items:center;justify-content:center}

/* intro */
.intro{left:0;top:770px;width:1200px;height:692px;background:var(--red)}
.intro h2{left:112px;top:144px;width:560px;color:var(--white);font-family:'Cinzel',Georgia,serif;font-weight:500;font-size:38px;line-height:50px}
.intro-copy{left:112px;top:305px;width:526px;color:var(--white);font-size:12.6px;line-height:21px;text-align:justify}
.intro-copy p+p{margin-top:20px}
.intro-photo{left:690px;top:165px;width:400px;height:436px;background:linear-gradient(160deg,#9fb4c9,#d8d4cc 55%,#6c8a4d)}

/* areas */
.areas{left:0;top:1462px;width:1200px;height:630px;background:var(--white)}
.area-list{list-style:none;font-family:'Cinzel',Georgia,serif;font-size:16px;color:#333}
.area-list li{height:33.2px;display:flex;align-items:flex-start}
.area-list li::before{content:"»";color:var(--red);font-family:'Roboto',sans-serif;font-size:17px;width:35px;line-height:17px}
.areas .col-a{left:185px;top:100px}
.areas .col-b{left:695px;top:100px}
.areas .divider{left:595px;top:92px;width:4px;height:440px;border-left:1px solid var(--red);border-right:1px solid var(--red)}

/* featured */
.featured{left:0;top:2092px;width:1200px;height:698px;background:var(--black)}
.section-title{font-family:'Cinzel',Georgia,serif;font-weight:500;text-align:center;width:1200px;left:0}
.featured .section-title{top:90px;color:var(--white);font-size:30px}
.listing{top:152px;width:310px;height:438px;background:var(--white)}
.listing-photo{width:310px;height:225px}
.listing h3{position:absolute;left:28px;top:248px;width:270px;font-size:20px;line-height:26px;font-weight:700;color:#222}
.listing .addr{position:absolute;left:30px;font-size:12.5px;color:#555;line-height:18px;width:260px}
.spec{position:absolute;font-size:10.5px;color:#333}
.spec b{color:var(--red);font-weight:400}
.arrow-btn{width:40px;height:40px;border-radius:50%;background:var(--white);display:flex;align-items:center;justify-content:center}

/* community */
.community{left:0;top:2790px;width:1200px;height:707px;background:var(--white)}
.com-photo-a{left:0;top:167px;width:160px;height:380px;background:linear-gradient(135deg,#6e4a33,#b88b62 60%,#d7c7b2)}
.com-photo-b{left:205px;top:130px;width:366px;height:454px;background:linear-gradient(180deg,#e7e9ea,#a9b1b6 55%,#4b5258)}
.community h2{left:610px;top:140px;font-family:'Cinzel',Georgia,serif;font-weight:500;font-size:46px;line-height:56px;color:#222}
.res{left:614px;width:400px}
.res h4{font-size:12.5px;color:var(--red);font-weight:700}
.res p{font-size:12.5px;line-height:20px;color:#666;margin-top:12px}
.btn-red{background:var(--red);color:var(--white);font-size:12px;font-weight:700;display:flex;align-items:center;justify-content:center}

/* prospect */
.prospect{left:0;top:3497px;width:1200px;height:760px;background:var(--red)}
.prospect .section-title{top:106px;color:var(--white);font-size:44px}
.tab{top:168px;width:155px;height:36px;background:var(--grey-tab);color:var(--white);font-size:12px;display:flex;align-items:center;justify-content:center}
.pcard{top:213px;width:310px;height:435px;background:var(--white);text-align:center}
.pcard-photo{width:310px;height:245px}
.pcard h3{margin-top:22px;font-size:20px;font-weight:700;color:#222}
.pcard p{margin:10px auto 0;width:250px;font-size:12.5px;line-height:21px;color:#666}
.pcard a{display:inline-block;margin-top:16px;font-size:12.5px;font-weight:700;color:var(--red);text-decoration:underline}
.arrow-soft{width:40px;height:40px;border-radius:50%;background:#d5444a;display:flex;align-items:center;justify-content:center}

/* contact */
.contact{left:0;top:4257px;width:1200px;height:605px;background:var(--white)}
.contact .section-title{top:122px;font-size:44px;color:#222}
.field{width:406px;height:60px;border:1px solid #cfcfcf;border-radius:4px;font-size:12.5px;color:#666;padding:0 18px;display:flex;align-items:center}
.textarea{left:612px;top:190px;width:406px;height:212px;align-items:flex-start;padding-top:22px}
.send{left:612px;top:421px;width:406px;height:60px;border-radius:4px}

/* footer */
.footer{left:0;top:4862px;width:1200px;height:397px;background:linear-gradient(180deg,#101010,#262626 70%,#1a1a1a)}
.footer .brand{left:150px;top:125px;width:190px}
.footer .brand-name,.footer .brand-tag{color:var(--white)}
.footer .brand-name{font-size:24px}
.footer .social{left:152px;top:190px}
.footer .social span{border-color:var(--white)}
.fcol h5{font-size:20px;font-weight:700;color:var(--white)}
.fcol ul{list-style:none;margin-top:26px}
.fcol li{font-size:13.5px;color:var(--white);line-height:21.5px}
.fcontact{left:832px;top:98px}
.citem{display:flex;gap:16px;color:var(--white);font-size:13.5px;line-height:20px;margin-bottom:22px;align-items:flex-start}
.ci{width:28px;height:28px;border-radius:50%;background:var(--white);flex:none;display:flex;align-items:center;justify-content:center}
.copyright{left:0;top:5212px;width:1200px;text-align:center;color:var(--white);font-size:13.5px}
</style>
</head>
<body>

<header class="header abs">
  <div class="brand abs">
    <span class="brand-name">BRIGHTHOLD</span>
    <span class="brand-tag">PROPERTY MANAGEMENT &amp; SERVICES</span>
  </div>
  <div class="social abs"><span></span><span></span><span></span></div>
  <div class="call abs">
    <svg width="34" height="34" viewBox="0 0 24 24" fill="none" stroke="#c0171f" stroke-width="1.6"><path d="M5 3h4l2 5-2.5 1.5a11 11 0 0 0 6 6L16 13l5 2v4a2 2 0 0 1-2 2A16 16 0 0 1 3 5a2 2 0 0 1 2-2z"/><path d="M14 3a7 7 0 0 1 7 7M14 6.5a3.5 3.5 0 0 1 3.5 3.5"/></svg>
    <div><small>Call Us Today :</small><strong>(916) 555-0142</strong></div>
  </div>
  <nav class="nav abs">
    <a class="active">HOME</a><a>LISTINGS</a><a>OWNERS</a><a>PROSPECT TENANTS</a><a>ABOUT</a><a>COMMUNITY</a><a>MORTGAGE INFO</a>
  </nav>
</header>

<section class="hero abs" role="img" aria-label="Photo of a smiling family arriving at the door of their new home"></section>
<h1 class="hero-title abs">BRIGHTHOLD<br>PROPERTY<br>MANAGEMENT</h1>
<div class="btn-light abs">GET STARTED</div>

<section class="intro abs">
  <h2 class="abs">PROPERTY MANAGEMENT ELK GROVE, SACRAMENTO &amp; SURROUNDING AREAS</h2>
  <div class="intro-copy abs">
    <p>Having the right property manager means having an agent who is committed to helping you and making being a home provider hassle free. I believe clear communication, work ethic, time management, staying focused and knowledge goes a long way in my business. This commitment level has helped us build a remarkable track record of delivering results and maintaining a long lasting business partnership with our clients.</p>
    <p>Additionally whether you are an experienced investor or a first time home seller or buyer, we can help you in finding the property of your dreams. We truly feel excited and gratified when helping individuals meet their real estate needs. You can count on us to always do what's in your best interest. We pride ourselves on being honest, trustworthy, and knowledgeable in the real estate market. We know how important it is to find your dream home or receive the best offer for your property. Therefore we will make it our responsibility to help you achieve those goals.</p>
  </div>
  <div class="intro-photo abs" role="img" aria-label="Photo of a two-storey house with a for rent sign on the lawn"></div>
</section>

<div class="slide-ctrl abs">
  <svg width="28" height="12" viewBox="0 0 28 12" fill="none" stroke="#fff" stroke-width="2"><path d="M7 1 2 6l5 5M21 1l5 5-5 5"/></svg>
  NEXT SLIDE
</div>
<div class="subscribe abs" style="height:56px;background:transparent;box-shadow:none"></div>
<div class="abs" style="left:660px;top:718px;width:540px;height:56px;background:#fff;box-shadow:0 6px 14px rgba(0,0,0,.15)">
  <div class="subscribe-input abs" style="top:14px;height:0"></div>
</div>
<div class="abs" style="left:694px;top:732px;width:334px;height:56px;background:#f1f1f1;color:#999;font-size:12px;display:flex;align-items:center;padding-left:26px">Enter email address</div>
<div class="abs btn-red" style="left:1028px;top:732px;width:144px;height:56px">SEARCH NOW</div>

<section class="areas abs">
  <ul class="area-list col-a abs">
    <li>SACRAMENTO</li><li>ANTELOPE</li><li>CARMICHAEL</li><li>CITRUS HEIGHTS</li><li>EL DORADO COUNTY</li><li>EL DORADO HILLS</li><li>ELVERTA</li><li>FAIR OAKS</li><li>FOLSOM</li><li>FOOTHILL FARMS</li><li>FLORIN VICINITY</li><li>LAND PARK / CURTIS PARK</li><li>GALT</li>
  </ul>
  <div class="divider abs"></div>
  <ul class="area-list col-b abs">
    <li>ELK GROVE / LAGUNA</li><li>MATHER</li><li>NATOMAS</li><li>NORTH HIGHLANDS</li><li>ORANGEVALE</li><li>RANCHO CORDOVA / GOLD RIVER</li><li>RANCHO CORDOVA / ANATOLIA &amp; VICINITY</li><li>RANCHO MURIETA</li><li>RIO LINDA</li><li>ROCKLIN</li><li>ROSEMONT / MAYHEW VICINITY</li><li>ROSEVILLE</li><li>WEST SACRAMENTO</li>
  </ul>
</section>

<section class="featured abs">
  <h2 class="section-title abs">FEATURED LISTINGS</h2>
  <div class="arrow-btn abs" style="left:35px;top:336px"><svg width="10" height="14" viewBox="0 0 10 14" fill="none" stroke="#222" stroke-width="2"><path d="M8 1 2 7l6 6"/></svg></div>
  <div class="arrow-btn abs" style="left:1124px;top:336px"><svg width="10" height="14" viewBox="0 0 10 14" fill="none" stroke="#222" stroke-width="2"><path d="m2 1 6 6-6 6"/></svg></div>

  <article class="listing abs" style="left:110px">
    <div class="listing-photo" role="img" aria-label="Photo of a tan apartment building under a blue sky" style="background:linear-gradient(180deg,#7fa7d6,#c9b68e 55%,#8a8a6a)"></div>
    <h3>Fantastic opportunity 2 Bdrm x 1 Bth ADU Unit!!</h3>
    <div class="addr" style="top:308px">2240 Linden Ave Oakland, CA 94621</div>
    <div class="spec" style="left:30px;top:338px"><b>Status</b> : Available</div>
    <div class="spec" style="left:30px;top:363px"><b>Type</b> &nbsp;: Residential</div>
    <div class="spec" style="left:160px;top:342px"><b>Size</b> <span style="margin-left:48px">: 693 Sq. Ft.</span></div>
    <div class="spec" style="left:160px;top:367px"><b>Bedrooms</b> <span style="margin-left:18px">: 2</span></div>
    <div class="spec" style="left:160px;top:392px"><b>Bathrooms</b> <span style="margin-left:13px">: 1</span></div>
  </article>

  <article class="listing abs" style="left:444px">
    <div class="listing-photo" role="img" aria-label="Photo of a single-storey ranch house with trees" style="background:linear-gradient(180deg,#6f9fd8,#a9b59a 55%,#6b7a4c)"></div>
    <h3>Fantastic opportunity 2 Bdrm x 1 Bth ADU Unit!!</h3>
    <div class="addr" style="top:304px">7410 Birch Ln #3 Carmichael,<br>CA 95608</div>
    <div class="spec" style="left:30px;top:348px"><b>Status</b> : Available</div>
    <div class="spec" style="left:30px;top:373px"><b>Type</b> &nbsp;: Residential</div>
    <div class="spec" style="left:160px;top:352px"><b>Size</b> <span style="margin-left:48px">: 1,350 Sq. Ft.</span></div>
    <div class="spec" style="left:160px;top:377px"><b>Bedrooms</b> <span style="margin-left:18px">: 2</span></div>
    <div class="spec" style="left:160px;top:402px"><b>Bathrooms</b> <span style="margin-left:13px">: 1</span></div>
  </article>

  <article class="listing abs" style="left:778px">
    <div class="listing-photo" role="img" aria-label="Photo of an empty bright room with wood floor" style="background:linear-gradient(180deg,#ececec,#d9d6d2 60%,#8a5a3c)"></div>
    <h3>Nice &amp; Clean 3 bd. x 1 bth. Apartment.</h3>
    <div class="addr" style="top:308px">Sacramento, CA 95818 Sacramento,</div>
    <div class="spec" style="left:30px;top:338px"><b>Status</b> : Rented</div>
    <div class="spec" style="left:30px;top:363px"><b>Type</b> &nbsp;: Residential</div>
    <div class="spec" style="left:160px;top:342px"><b>Size</b> <span style="margin-left:48px">: 693 Sq. Ft.</span></div>
    <div class="spec" style="left:160px;top:367px"><b>Bedrooms</b> <span style="margin-left:18px">: 3</span></div>
    <div class="spec" style="left:160px;top:392px"><b>Bathrooms</b> <span style="margin-left:13px">: 1</span></div>
  </article>
</section>

<section class="community abs">
  <div class="com-photo-a abs" role="img" aria-label="Photo of hands holding a small model house"></div>
  <div class="com-photo-b abs" role="img" aria-label="Photo of business people meeting in a bright office"></div>
  <h2 class="abs">COMMUNITY<br>RESOURCES</h2>
  <div class="res abs" style="top:263px"><h4>Neighborly Communities</h4><p>Search Neighborly neighborhood profiles!</p></div>
  <div class="res abs" style="top:328px"><h4>Regional Education Data Center</h4><p>REDC is the primary federal entity for collecting and analyzing data that are related to education in the United States and other nations.</p></div>
  <div class="res abs" style="top:440px"><h4>SchoolCompass.net</h4><p>SchoolCompass.net is your objective source of school information on elementary, middle and high schools.</p></div>
  <div class="btn-red abs" style="left:614px;top:532px;width:152px;height:42px">READ MORE</div>
</section>

<section class="prospect abs">
  <h2 class="section-title abs">PROSPECT TENANTS</h2>
  <div class="tab abs" style="left:188px">TENANT</div>
  <div class="tab abs" style="left:522px">RESIDENTS</div>
  <div class="tab abs" style="left:837px;width:190px">PROPERTY MANAGERS</div>
  <div class="arrow-soft abs" style="left:35px;top:410px"><svg width="10" height="14" viewBox="0 0 10 14" fill="none" stroke="#fff" stroke-width="2"><path d="M8 1 2 7l6 6"/></svg></div>
  <div class="arrow-soft abs" style="left:1124px;top:410px"><svg width="10" height="14" viewBox="0 0 10 14" fill="none" stroke="#fff" stroke-width="2"><path d="m2 1 6 6-6 6"/></svg></div>

  <article class="pcard abs" style="left:110px">
    <div class="pcard-photo" role="img" aria-label="Photo of a tablet and a small model house on a desk" style="background:linear-gradient(160deg,#5b5f63,#b9b6b2 60%,#eee)"></div>
    <h3>Tenant Application</h3>
    <p>In order to rent a residential home from Brighthold Property Management Inc., applicants must be</p>
    <a>Read More ➜</a>
  </article>
  <article class="pcard abs" style="left:444px">
    <div class="pcard-photo" role="img" aria-label="Photo of a hand pointing at a property management graphic" style="background:linear-gradient(160deg,#4a3360,#8a6aa0 55%,#c7b9d2)"></div>
    <h3>For Residents</h3>
    <p>We know you have a choice in places to live and we sincerely appreciate your choice to live in one of our</p>
    <a>Read More ➜</a>
  </article>
  <article class="pcard abs" style="left:778px">
    <div class="pcard-photo" role="img" aria-label="Photo of a family walking into their new home" style="background:linear-gradient(100deg,#4a4640,#a49d94 50%,#e2ddd6)"></div>
    <h3>Dream Home Finder</h3>
    <p>For detailed information on buying a home or property, please complete the form below describing</p>
    <a>Read More ➜</a>
  </article>
</section>

<section class="contact abs">
  <h2 class="section-title abs">CONTACT US</h2>
  <div class="field abs" style="left:183px;top:190px">Name</div>
  <div class="field abs" style="left:183px;top:267px">Company name</div>
  <div class="field abs" style="left:183px;top:344px">Email</div>
  <div class="field abs" style="left:183px;top:421px">Phone</div>
  <div class="field textarea abs">Text here...</div>
  <div class="btn-red send abs">SEND NOW</div>
</section>

<footer class="footer abs">
  <div class="brand abs">
    <span class="brand-name">BRIGHTHOLD</span>
    <span class="brand-tag">PROPERTY MANAGEMENT &amp; SERVICES</span>
  </div>
  <div class="social abs"><span></span><span></span><span></span></div>
  <div class="fcol abs" style="left:460px;top:98px">
    <h5>Quick Links</h5>
    <ul><li>Listings</li><li>Owners</li><li>Prospect Tenants</li><li>About</li><li>Community</li><li>Mortgage Info</li></ul>
  </div>
  <div class="fcol abs" style="left:640px;top:98px">
    <h5>Support</h5>
    <ul><li>Privacy policy</li><li>Terms of Service</li><li>Faq</li><li>Contact</li><li>Blog</li><li>Support</li></ul>
  </div>
  <div class="fcol fcontact abs">
    <h5>Contact Us</h5>
    <div style="margin-top:26px">
      <div class="citem"><span class="ci"><svg width="12" height="15" viewBox="0 0 12 15"><path d="M6 0a6 6 0 0 1 6 6c0 4-6 9-6 9S0 10 0 6a6 6 0 0 1 6-6z" fill="#c0171f"/><circle cx="6" cy="6" r="2" fill="#fff"/></svg></span><span>4810 Alder Crest Rd. #112<br>Sacramento, CA. 95822</span></div>
      <div class="citem"><span class="ci" style="border-radius:4px;background:#c0171f"><svg width="14" height="10" viewBox="0 0 14 10" fill="none" stroke="#fff" stroke-width="1.4"><rect x=".7" y=".7" width="12.6" height="8.6"/><path d="m1 1 6 5 6-5"/></svg></span><span style="padding-top:4px">(916) 555-0187</span></div>
      <div class="citem"><span class="ci"><svg width="14" height="14" viewBox="0 0 24 24"><path d="M5 3h4l2 5-2.5 1.5a11 11 0 0 0 6 6L16 13l5 2v4a2 2 0 0 1-2 2A16 16 0 0 1 3 5a2 2 0 0 1 2-2z" fill="#c0171f"/></svg></span><span style="padding-top:4px">tom.hale@brighthold.biz</span></div>
    </div>
  </div>
  <div class="copyright abs" style="top:350px">© Copyrights 2024 Company name | All Rights Reserved | Privacy Policy</div>
</footer>

</body>
</html>
```